Keystone ridge construction brochure

i would like a brochure that can be send to clients digitally and printed. we are a geotechnical, foundation, and concrete company. I attached info below

Target Market(s)

Construction managers, general contractors, developers, municipalities, private, and commercial partners.

Industry/Entity Type

Geotechnical / foundation

Font styles to use
Serif
Other font styles liked:
• Maybe same as logo

Colors
0054AA
0677BA
7BADD7
CADEEF
E8F1F8

```html
<!DOCTYPE html>
<html lang="en">
<head>
<meta charset="utf-8">
<title>Keystone Ridge Construction – Brochure</title>
<link href="https://fonts.googleapis.com/css2?family=Hind:wght@400;500;600;700&family=Roboto+Slab:wght@500;600;700&display=swap" rel="stylesheet">
<style>
:root{
  --stage:#bdbdbf;
  --blue-deep:#0054aa;
  --blue-mid:#0677ba;
  --blue-soft:#7badd7;
  --blue-pale:#cadeef;
  --blue-mist:#e8f1f8;
  --ink:#2b2f38;
  --white:#ffffff;
}
*{box-sizing:border-box;margin:0;padding:0}
html,body{width:947px;height:1200px;overflow:hidden}
body{background:var(--stage);position:relative;font-family:"Hind",sans-serif;color:var(--ink)}
.serif{font-family:"Roboto Slab",serif}
.page{position:absolute;width:408px;height:528px;background:var(--white);overflow:hidden}
.page--cover{left:45px;top:59px;background:var(--blue-deep)}
.page--about{left:490px;top:59px}
.page--services{left:45px;top:613px}
.page--projects{left:490px;top:613px}

/* cover */
.cover-art{position:absolute;left:0;top:0}
.brand-plate{position:absolute;left:33px;top:50px;width:184px;height:30px;background:var(--blue-deep);border:1.5px solid var(--white);color:var(--white);font-family:"Roboto Slab",serif;font-weight:700;font-size:16px;line-height:28px;text-align:center;letter-spacing:.6px}
.hanger{position:absolute;top:0;width:1px;height:50px;background:var(--blue-deep)}
.cover-title{position:absolute;left:33px;top:318px;font-family:"Roboto Slab",serif;font-weight:700;font-size:25px;line-height:33.5px;color:var(--white)}
.cover-sub{position:absolute;left:33px;top:423px;font-size:12.4px;line-height:17.5px;color:var(--white);font-weight:400}
.cover-sub b{font-weight:600}
.cover-dash{position:absolute;left:33px;top:464px;width:26px;height:2px;background:var(--blue-pale)}
.cover-web{position:absolute;left:33px;top:488px;font-size:7px;color:var(--white);letter-spacing:.6px;display:flex;align-items:center;gap:3px}

/* inner pages */
.tagline{position:absolute;left:33px;top:31px;width:342px;display:flex;align-items:flex-end;gap:2px;font-family:"Roboto Slab",serif;font-size:8.2px;font-weight:600;color:var(--blue-deep)}
.tagline::after{content:"";flex:1;height:0;border-bottom:.6px solid var(--blue-soft);margin-bottom:3px}
.section-title{position:absolute;left:33px;font-family:"Roboto Slab",serif;font-weight:700;color:var(--blue-deep);font-size:18px;line-height:1}
.chip{position:absolute;left:33px;top:91.5px;height:17.5px;background:var(--blue-mist);font-size:10.4px;line-height:19px;padding:0 4px;color:var(--ink)}
.body-copy{position:absolute;left:33px;width:171px;font-size:7.85px;line-height:12.1px;text-align:justify;color:var(--ink)}
.photo{position:absolute}

.mission-band{position:absolute;left:33px;top:271px;width:342px;height:29px;background:var(--blue-mist);display:flex;align-items:center;gap:6px;padding-left:7px;font-family:"Roboto Slab",serif;font-size:13.5px;font-weight:600;color:var(--blue-deep)}
.mission-copy{position:absolute;left:33px;top:313px;width:342px;font-size:8px;line-height:12.2px;text-align:justify}

.stat{position:absolute;background:var(--blue-mist);display:flex;align-items:center;gap:6px;padding-left:6px}
.stat-num{font-family:"Roboto Slab",serif;font-size:12px;font-weight:600;color:var(--blue-deep);line-height:1.15}
.stat-label{font-size:8px;color:var(--ink);line-height:1.3}

.footer-brand{position:absolute;left:33px;top:476px;font-family:"Roboto Slab",serif;font-size:7.4px;font-weight:700;color:var(--blue-deep);line-height:8.4px;letter-spacing:.3px}
.footer-rule{position:absolute;left:80px;top:487px;width:288px;border-top:.6px solid var(--blue-soft)}
.folio{position:absolute;left:369px;top:483px;font-size:5px;color:var(--blue-deep)}
.skyline{position:absolute;left:0;bottom:0;width:408px;height:32px;background:linear-gradient(to bottom,rgba(232,241,248,0),var(--blue-mist))}

/* services */
.service{position:absolute;border:.8px solid var(--blue-soft);padding:8px 8px 0 8px}
.service-head{display:flex;align-items:center;gap:6px;height:26px}
.service-name{font-family:"Roboto Slab",serif;font-size:9.2px;line-height:11.8px;font-weight:600;color:var(--blue-deep)}
.service-desc{margin-top:8px;font-size:8px;line-height:12px;color:var(--ink)}
.cap-title{position:absolute;left:33px;top:283px;font-family:"Roboto Slab",serif;font-size:13px;font-weight:700;color:var(--blue-deep)}
.cap-list{position:absolute;left:33px;top:311px;list-style:none}
.cap-list li{display:flex;align-items:center;gap:4px;font-size:8px;height:21.4px;color:var(--ink)}

/* projects */
.project{position:absolute;width:168px;height:114.5px;border:.8px solid var(--blue-soft);background:var(--white)}
.project-photo{width:100%;height:75px}
.project-name{margin:6px 0 0 4.5px;font-family:"Roboto Slab",serif;font-size:8.8px;font-weight:600;color:var(--blue-deep);line-height:1.1}
.project-meta{margin:3px 0 0 4.5px;font-size:7.9px;color:var(--ink)}
</style>
</head>
<body>

<!-- Cover -->
<section class="page page--cover">
  <svg class="cover-art" width="408" height="528" viewBox="0 0 408 528">
    <defs>
      <linearGradient id="siteTone" x1="0" y1="0" x2="1" y2="1">
        <stop offset="0" stop-color="#9fd0f2"/>
        <stop offset=".45" stop-color="#b9c2c4"/>
        <stop offset="1" stop-color="#8a8a84"/>
      </linearGradient>
    </defs>
    <rect width="408" height="420" fill="url(#siteTone)" role="img" aria-label="Engineers in hard hats reviewing foundation and concrete work on a building site, with scaffolding and cranes"/>
    <path d="M0,270 C110,245 230,265 408,385 L408,528 L0,528Z" fill="#0677ba"/>
    <path d="M0,284 C120,262 240,290 408,400 L408,528 L0,528Z" fill="#e8f1f8"/>
    <path d="M0,287 C120,266 236,296 408,409 L408,528 L0,528Z" fill="#0054aa"/>
  </svg>
  <div class="hanger" style="left:49px"></div>
  <div class="hanger" style="left:196px"></div>
  <div class="brand-plate">KEYSTONE RIDGE</div>
  <h1 class="cover-title">Building<br>Foundations.<br>Building Futures.</h1>
  <p class="cover-sub">Excellence in Geotechnical, Foundation<br>&amp; Concrete Construction <b>Since 1998</b></p>
  <div class="cover-dash"></div>
  <div class="cover-web">
    <svg width="8" height="8" viewBox="0 0 10 10" fill="none" stroke="#fff" stroke-width="1"><circle cx="5" cy="5" r="4"/><ellipse cx="5" cy="5" rx="1.8" ry="4"/><path d="M1 5h8"/></svg>
    www.keystoneridgebuild.com
  </div>
</section>

<!-- Who we are -->
<section class="page page--about">
  <div class="tagline">Building Foundations.Building Futures.</div>
  <h2 class="section-title" style="top:69px">WHO WE ARE</h2>
  <div class="chip">Your Trusted Foundation Partner</div>
  <p class="body-copy" style="top:119px">For over 25 years, Keystone Ridge Construction Group has delivered the ground beneath landmark projects across commercial, municipal, and industrial sectors. Like bedrock, we provide the stability &amp; strength your structure demands — from soil investigation to the final pour.</p>
  <p class="body-copy" style="top:200px">Our team of geotechnical engineers, foundation specialists, and concrete crews brings precision, innovation, and transparency to every site — ensuring your project rests on solid ground, on time and within budget.</p>
  <div class="photo" role="img" aria-label="Tower crane beside a high-rise concrete frame against a blue sky" style="left:223.5px;top:70px;width:151.5px;height:185px;background:linear-gradient(135deg,#0677ba 0%,#7badd7 45%,#c98a4a 70%,#6d7378 100%)"></div>

  <div class="mission-band">
    <svg width="22" height="22" viewBox="0 0 22 22" fill="none" stroke="#0677ba" stroke-width="1.4"><circle cx="11" cy="11" r="9.5"/><circle cx="11" cy="11" r="6"/><circle cx="11" cy="11" r="2.5"/><path d="M11 11 L19 3 M16 3h3v3"/></svg>
    Our Mission
  </div>
  <p class="mission-copy">To set every project on solid ground — delivering foundations and concrete that stand the test of time through sound engineering, craftsmanship, and an unwavering commitment to our partners.</p>

  <div class="stat" style="left:33px;top:353px;width:99px;height:46px">
    <svg width="24" height="24" viewBox="0 0 24 24" fill="none" stroke="#0677ba" stroke-width="1.1"><rect x="2" y="4" width="20" height="5"/><path d="M5 9v13M12 9v13M19 9v13M3 22h4M10 22h4M17 22h4"/></svg>
    <div><div class="stat-num">500+</div><div class="stat-label">Foundations Built</div></div>
  </div>
  <div class="stat" style="left:136px;top:353px;width:104px;height:46px">
    <svg width="24" height="24" viewBox="0 0 24 24" fill="none" stroke="#0677ba" stroke-width="1.2"><circle cx="10" cy="7" r="4.5"/><path d="M2 21c0-5 4-8 8-8 2 0 3 .4 4 1"/><circle cx="18" cy="18" r="4"/><path d="M16 18l1.5 1.5L20 17"/></svg>
    <div><div class="stat-num">25+</div><div class="stat-label">Years Active</div></div>
  </div>
  <div class="stat" style="left:243px;top:353px;width:132px;height:46px">
    <svg width="26" height="24" viewBox="0 0 26 24" fill="none" stroke="#0677ba" stroke-width="1"><path d="M4 4l1 2 2 .3-1.5 1.4.4 2L4 8.7 2.1 9.7l.4-2L1 6.3 3 6z"/><path d="M13 3l1 2 2 .3-1.5 1.4.4 2L13 7.7l-1.9 1 .4-2L10 5.3 12 5z"/><path d="M22 4l1 2 2 .3-1.5 1.4.4 2L22 8.7l-1.9 1 .4-2L19 6.3 21 6z"/><circle cx="7" cy="14" r="2.2"/><circle cx="13" cy="13" r="2.4"/><circle cx="19" cy="14" r="2.2"/><path d="M3 21c0-3 2-4.5 4-4.5M9 21c0-3 2-5 4-5s4 2 4 5M23 21c0-3-2-4.5-4-4.5"/></svg>
    <div><div class="stat-num">98%</div><div class="stat-label">Client Satisfaction</div></div>
  </div>
  <div class="stat" style="left:33px;top:406px;width:99px;height:46px">
    <svg width="24" height="24" viewBox="0 0 24 24" fill="none" stroke="#0677ba" stroke-width="1.1"><path d="M2 7h20M2 12h20M2 17h20"/><circle cx="6" cy="9.5" r=".8"/><circle cx="15" cy="14.5" r=".8"/><circle cx="10" cy="19.5" r=".8"/><path d="M12 2v20"/></svg>
    <div><div class="stat-num">8,000+</div><div class="stat-label">Borings Logged</div></div>
  </div>
  <div class="stat" style="left:136px;top:406px;width:104px;height:46px">
    <svg width="26" height="26" viewBox="0 0 26 26" fill="none" stroke="#0677ba" stroke-width="1.1"><path d="M1 24h24"/><rect x="3" y="17" width="3" height="7"/><rect x="8" y="14" width="3" height="10"/><rect x="13" y="11" width="3" height="13"/><rect x="18" y="8" width="3" height="16"/><path d="M2 14 L10 8 L14 10 L23 2 M19 2h4v4"/></svg>
    <div><div class="stat-num">1.2M</div><div class="stat-label">Cubic Yards Poured</div></div>
  </div>
  <div class="stat" style="left:243px;top:406px;width:132px;height:46px">
    <svg width="28" height="24" viewBox="0 0 28 24" fill="none" stroke="#0677ba" stroke-width="1.1"><path d="M14 1v4M8 3l2 3M20 3l-2 3"/><path d="M1 11h4v9H1M27 11h-4v9h4"/><path d="M5 12l5-2 4 2 4-2 5 2M5 18l3 1 3 2 2-1 3 1 3-2 4-1"/><path d="M12 13l3 3M14 12l4 4"/></svg>
    <div><div class="stat-num">100%</div><div class="stat-label">Safety Commitment</div></div>
  </div>

  <div class="skyline" role="img" aria-label="Faint city skyline with cranes"></div>
  <div class="footer-brand">KEYSTONE<br>RIDGE</div>
  <div class="footer-rule"></div>
  <div class="folio">02</div>
</section>

<!-- Services -->
<section class="page page--services">
  <div class="tagline">Building Foundations.Building Futures.</div>
  <h2 class="section-title" style="top:67px">Our Core Services</h2>
  <div class="chip">What We Build On</div>

  <div class="service" style="left:33px;top:119px;width:170.5px;height:74px">
    <div class="service-head">
      <svg width="24" height="24" viewBox="0 0 24 24" fill="none" stroke="#0054aa" stroke-width="1.1"><path d="M2 8h20M2 13h20M2 18h20"/><path d="M12 1v21M9 4l3-3 3 3"/></svg>
      <div class="service-name">Geotechnical<br>Investigation</div>
    </div>
    <p class="service-desc">Soil borings, lab testing, site characterization, and engineering reports.</p>
  </div>
  <div class="service" style="left:206px;top:119px;width:169px;height:74px">
    <div class="service-head">
      <svg width="24" height="24" viewBox="0 0 24 24" fill="none" stroke="#0054aa" stroke-width="1.1"><rect x="2" y="3" width="20" height="5"/><path d="M6 8v14M12 8v14M18 8v14M4 20l2 2 2-2M10 20l2 2 2-2M16 20l2 2 2-2"/></svg>
      <div class="service-name">Deep<br>Foundations</div>
    </div>
    <p class="service-desc">Driven piles, drilled shafts, micropiles, and caissons for heavy loads.</p>
  </div>
  <div class="service" style="left:33px;top:198px;width:170.5px;height:74px">
    <div class="service-head">
      <svg width="24" height="24" viewBox="0 0 24 24" fill="none" stroke="#0054aa" stroke-width="1.1"><rect x="2" y="14" width="20" height="7"/><path d="M5 14V9h14v5M8 9V5h8v4"/><path d="M6 17.5h4M14 17.5h4"/></svg>
      <div class="service-name">Concrete<br>Construction</div>
    </div>
    <p class="service-desc">Footings, mat slabs, structural walls, and cast-in-place flatwork.</p>
  </div>
  <div class="service" style="left:206px;top:198px;width:169px;height:74px">
    <div class="service-head">
      <svg width="24" height="24" viewBox="0 0 24 24" fill="none" stroke="#0054aa" stroke-width="1.1"><path d="M3 3v19h18"/><path d="M3 8h6M3 13h10M3 18h14"/><path d="M9 8l4 5 4 5"/></svg>
      <div class="service-name">Earth Retention<br>&amp; Ground Work</div>
    </div>
    <p class="service-desc">Shoring, soil nailing, underpinning, and ground improvement systems.</p>
  </div>

  <h3 class="cap-title">Specialized Capabilities</h3>
  <ul class="cap-list">
    <li><svg width="7" height="7" viewBox="0 0 10 10" fill="none" stroke="#0677ba" stroke-width="1"><circle cx="5" cy="5" r="4.3"/><path d="M3 5.2l1.4 1.4L7 3.8"/></svg>Pile load testing &amp; integrity verification</li>
    <li><svg width="7" height="7" viewBox="0 0 10 10" fill="none" stroke="#0677ba" stroke-width="1"><circle cx="5" cy="5" r="4.3"/><path d="M3 5.2l1.4 1.4L7 3.8"/></svg>Design-build foundation packages</li>
    <li><svg width="7" height="7" viewBox="0 0 10 10" fill="none" stroke="#0677ba" stroke-width="1"><circle cx="5" cy="5" r="4.3"/><path d="M3 5.2l1.4 1.4L7 3.8"/></svg>Foundation repair and structural underpinning</li>
    <li><svg width="7" height="7" viewBox="0 0 10 10" fill="none" stroke="#0677ba" stroke-width="1"><circle cx="5" cy="5" r="4.3"/><path d="M3 5.2l1.4 1.4L7 3.8"/></svg>Dewatering, grouting &amp; soil stabilization</li>
    <li><svg width="7" height="7" viewBox="0 0 10 10" fill="none" stroke="#0677ba" stroke-width="1"><circle cx="5" cy="5" r="4.3"/><path d="M3 5.2l1.4 1.4L7 3.8"/></svg>Concrete testing &amp; quality control</li>
  </ul>
  <div class="photo" role="img" aria-label="Hard hat resting on a table in front of buildings under construction" style="left:252px;top:284.5px;width:123px;height:176.5px;background:linear-gradient(180deg,#cadeef 0%,#7badd7 45%,#c7a24a 75%,#9c8066 100%)"></div>

  <div class="skyline" role="img" aria-label="Faint city skyline with cranes"></div>
  <div class="footer-brand">KEYSTONE<br>RIDGE</div>
  <div class="footer-rule"></div>
  <div class="folio">03</div>
</section>

<!-- Projects -->
<section class="page page--projects">
  <div class="tagline">Building Foundations.Building Futures.</div>
  <h2 class="section-title" style="top:67px">Our Featured Projects</h2>
  <div class="chip">Our Portfolio</div>

  <article class="project" style="left:33px;top:119px">
    <div class="project-photo" role="img" aria-label="Glass high-rise towers under a deep blue sky" style="background:linear-gradient(180deg,#0054aa 0%,#7badd7 60%,#6b6a6a 100%)"></div>
    <div class="project-name">Skyline Corporate Tower</div>
    <div class="project-meta">Drilled Shafts&nbsp; | &nbsp;24 Floors&nbsp; | &nbsp;2023</div>
  </article>
  <article class="project" style="left:206px;top:119px">
    <div class="project-photo" role="img" aria-label="White residential apartment blocks with trees" style="background:linear-gradient(180deg,#7badd7 0%,#e8f1f8 50%,#6f8f5a 100%)"></div>
    <div class="project-name">Greenview Residential Estates</div>
    <div class="project-meta">Mat Foundations&nbsp; | &nbsp;320 Units&nbsp; | &nbsp;2022</div>
  </article>
  <article class="project" style="left:33px;top:236px">
    <div class="project-photo" role="img" aria-label="Light-rail train at a city station platform" style="background:linear-gradient(180deg,#8a9196 0%,#c8343a 55%,#6d6f72 100%)"></div>
    <div class="project-name">Metro Transit Hub Expansion</div>
    <div class="project-meta">Earth Retention&nbsp; | &nbsp;Phase 2&nbsp; | &nbsp;2022</div>
  </article>
  <article class="project" style="left:206px;top:236px">
    <div class="project-photo" role="img" aria-label="Waterfront city skyline across a river with a park" style="background:linear-gradient(180deg,#0677ba 0%,#cadeef 50%,#3f6f8a 70%,#4f8a3a 100%)"></div>
    <div class="project-name">Harborview Industrial Park</div>
    <div class="project-meta">Slab-on-Grade&nbsp; | &nbsp;450,000 sq ft&nbsp; | &nbsp;2021</div>
  </article>
  <article class="project" style="left:33px;top:354px">
    <div class="project-photo" role="img" aria-label="Illuminated hotel entrance at night" style="background:linear-gradient(180deg,#3a3027 0%,#c9923c 55%,#2c2620 100%)"></div>
    <div class="project-name">The Grand Meridian Hotel</div>
    <div class="project-meta">Driven Piles&nbsp; | &nbsp;350 Rooms&nbsp; | &nbsp;2021</div>
  </article>
  <article class="project" style="left:206px;top:354px">
    <div class="project-photo" role="img" aria-label="Steel arch pedestrian bridge over a river in autumn" style="background:linear-gradient(180deg,#cadeef 0%,#8f7a5a 50%,#5f6a70 100%)"></div>
    <div class="project-name">Riverside Pedestrian Bridge</div>
    <div class="project-meta">Micropiles&nbsp; | &nbsp;680m Span&nbsp; | &nbsp;2020</div>
  </article>

  <div class="skyline" role="img" aria-label="Faint city skyline with cranes"></div>
  <div class="footer-brand">KEYSTONE<br>RIDGE</div>
  <div class="footer-rule"></div>
  <div class="folio">04</div>
</section>

</body>
</html>
```